Website Design Chair in Business Administration, especially information and service systems

We, the Chair in Business Administration, especially information and service systems, teach in the field of Business Informatics and Business Administration at Velmont University.
We want to setup our current website in a fresh new and clean design because the design of the old page is outdated: http://dkp.uni-velmont.example/en/
The design should be created in a way that we can integrate it into Wordpress later. Furthermore, the website should have the existing website tabs (pages). We want to add the missing subcategories in the tabs, which means that when you move the mouse over a tab, subcategories/side menus should appear.
We have the goal that the website is very clear and that the students get a direct overview especially of the lectures offered. Furthermore the website should be suitable for mobile devices.
Start page:
In general we are interested in a Tile-based Design (2 or more columns) on the start page - similar to this page: https://www.hochschule-brandor.example/. Here, the fields (Digital Process Networks (DPN) with photo, Lectures of the semester, theses, study projects, projects, current events (social media wall), jobs and internship (together), new publications) should be integrated in the form of tiles with a cover picture per field and a short description.
Furthermore, we would like to position a search bar, a social media wall especially for Instagram (replaces the field current events) and the cooperation partners perhaps as sliders with logos of the companies in the lower part of the start page (see Cooperation tab on the far right) on the start page. Footer remains the same.
Research:
Display the same content more attractively.
Learning-Platform:
Furthermore only as link.
Teaching:
In addition to the existing sub-items (Lectures of the semester, teaching-archive, learning platform, theses and book lending), the "Overview of DPN courses" and the " Open Bachelor & Master theses" should be graphically displayed.
Team:
The concept of the Teamgraph including project connections should remain. Furthermore we can imagine to list the employees with photos and short description in form of tiles (1 employee on a tile) below the graph (2 or more columns of tiles).
Publications:
Continue to display a list of publications.
Jobs and internships:
The Open Positions should be divided here into Research Associates, Student Assistants and interns, so that it becomes clearer (3 columns).
Projects:
Here we are interested a Tile-based Design (2 or more columns). We want to integrate the project fields (KORUVAN, Tidal Record Vault etc.) in the form of tiles with a title image per field and a short description.
Events and cooperations should be removed as they are sufficiently represented on the start page.
Target Market(s)
Students as well as current and future project partners
Logo Text
DPN (+ optional Chair in Digital Process Networks)
Coding
Coded - Design and coding required
Number of Pages Required
5+ page
Requirements
Must have
- See description above
Nice to have
- Perhaps a design can be created in which a direct connection to research content (AI, Deep Learning etc.) and to courses (Data Science, AI in companies etc.) can be seen.

```html
<!DOCTYPE html>
<html lang="en">
<head>
<meta charset="utf-8">
<title>DPN – Start Page Variants</title>
<link href="https://fonts.googleapis.com/css2?family=Montserrat:wght@600;700;800&family=Roboto:wght@400;500;700&display=swap" rel="stylesheet">
<style>
:root{
  --navy:#0f3d9c;
  --navy-dark:#0b3288;
  --sky:#2a8ad4;
  --sky-soft:#dfe9f6;
  --ink:#1e2532;
  --muted:#6b7280;
  --stage:#e5e5e7;
  --panel:#eeeff1;
  --white:#ffffff;
}
*{box-sizing:border-box;margin:0;padding:0}
html,body{width:702px;height:1200px;overflow:hidden}
body{background:var(--stage);font-family:"Roboto",sans-serif;color:var(--ink);position:relative}
.page{position:absolute;width:637px;background:var(--white);transform:scale(0.4763);transform-origin:0 0;box-shadow:0 2px 8px rgba(0,0,0,.12)}
.page--hero{left:32px;top:38px}
.page--compact{left:366px;top:38px}

.site-header{height:51px;display:flex;align-items:center;padding:0 60px 0 58px}
.brand{display:flex;align-items:center;gap:9px}
.brand__name{font-family:"Montserrat",sans-serif;font-weight:700;font-size:19px;color:var(--navy);letter-spacing:.5px}
.brand__sub{border-left:1px solid #b9c4dc;padding-left:8px;font-size:7.5px;line-height:1.25;color:var(--navy)}
.header-tools{margin-left:auto;display:flex;align-items:center;gap:16px;font-size:6.5px;color:var(--ink)}
.lang b{color:var(--sky);font-weight:500}
.search{width:107px;height:20px;background:#eef1f6;border-radius:2px;display:flex;align-items:center;padding-left:8px;color:#8a93a5;font-size:6.5px}

.main-nav{height:23px;background:var(--navy);display:flex;align-items:stretch;padding-left:54px;gap:0}
.main-nav span{color:#fff;font-size:7px;font-weight:500;display:flex;align-items:center;padding:0 6.5px;letter-spacing:.2px}
.main-nav .is-active{background:var(--sky)}

.hero{height:288px;position:relative;background:linear-gradient(160deg,#8d98a8 0%,#5c6676 45%,#3b4250 100%)}
.hero__box{position:absolute;left:175px;top:36px;width:290px;height:105px;background:rgba(42,110,200,.78);text-align:center;color:#fff;padding-top:8px}
.hero__title{font-family:"Montserrat",sans-serif;font-weight:700;font-size:30px}
.hero__text{font-size:8px;line-height:1.7;margin-top:2px}
.hero__btn{position:absolute;left:265px;top:118px;width:108px;height:22px;border-radius:11px;background:var(--sky);color:#fff;font-size:7.5px;font-weight:700;display:flex;align-items:center;justify-content:center}
.arrow{position:absolute;width:20px;height:20px;border-radius:50%;border:1px solid currentColor;display:flex;align-items:center;justify-content:center;font-size:10px}
.hero .arrow{color:#fff;top:134px}

.welcome{display:flex;padding:0 54px;position:relative}
.page--hero .welcome{height:355px;padding-top:80px}
.page--compact .welcome{height:334px;padding-top:60px}
.welcome__text{width:240px;padding-top:27px}
.eyebrow{font-family:"Montserrat",sans-serif;font-weight:700;font-size:8.5px;color:var(--sky)}
.welcome h1{font-family:"Montserrat",sans-serif;font-weight:700;font-size:15.5px;color:var(--navy);line-height:1.3;margin:6px 0 16px}
.welcome p{font-size:7px;line-height:2;color:#4b5260;text-align:justify}
.welcome p u{color:var(--sky)}
.welcome__media{position:relative;margin-left:25px;width:276px;height:245px}
.welcome__frame{position:absolute;left:0;top:0;width:246px;height:120px;border:2px solid var(--sky);border-bottom:none;border-right-width:2px}
.welcome__photo{position:absolute;left:9px;top:9px;width:256px;height:234px;background:linear-gradient(170deg,#d9c6a3 0%,#9a8a74 50%,#3e4554 100%)}
.welcome__media .arrow{background:#fff;color:#444;border:none;top:116px;width:16px;height:16px;font-size:8px}

.section-title{font-family:"Montserrat",sans-serif;font-weight:700;color:var(--navy);text-align:center;font-size:17px;letter-spacing:.3px}
.lectures{height:195px;background:linear-gradient(135deg,#f1f2f4,#e3e5e9 50%,#f1f2f4);padding-top:30px}
.lecture-grid{display:flex;gap:9px;justify-content:center;margin-top:10px}
.lecture{width:123px;height:86px;background:#fff;display:flex;flex-direction:column;align-items:center;justify-content:center;gap:8px;font-size:8px;font-weight:500;text-align:center}
.lecture svg{width:36px;height:32px}

.theses{position:relative;height:260px}
.theses__band{height:150px;background:var(--navy);text-align:center;color:#fff;padding-top:28px}
.theses__band .section-title{color:#fff;font-size:19px}
.theses__band p{font-size:7px;line-height:1.7;margin-top:6px}
.theses-cards{position:absolute;top:96px;left:0;right:0;display:flex;gap:40px;justify-content:center}
.thesis{width:156px;height:108px;background:#fff;box-shadow:0 2px 6px rgba(0,0,0,.1);text-align:center;padding-top:10px}
.thesis__num{width:24px;height:24px;margin:0 auto;border-radius:50%;background:var(--sky);color:#fff;font-size:10px;font-weight:700;display:flex;align-items:center;justify-content:center}
.thesis h3{font-size:8.5px;color:var(--navy);margin:6px 0 4px;font-weight:700}
.thesis p{font-size:6.8px;line-height:1.8;color:var(--muted);padding:0 12px}

.projects{position:relative;padding-top:10px;height:293px}
.project-grid{display:flex;gap:14px;padding:0 60px;margin-top:14px}
.project{width:252px;position:relative;height:198px}
.project__photo{height:147px}
.project__photo--mall{background:linear-gradient(180deg,#b9a79a,#8c7a6d 60%,#d1c2b0)}
.project__photo--farm{background:linear-gradient(180deg,#8faed8 0%,#a7bbd0 40%,#6f8a47 70%,#556a33)}
.project__body{position:absolute;left:14px;right:14px;top:120px;background:#fff;box-shadow:0 2px 6px rgba(0,0,0,.08);text-align:center;padding:8px 10px}
.project__body h3{font-size:9px;font-weight:500;margin-bottom:6px}
.project__body p{font-size:6.8px;line-height:1.8;color:var(--muted)}
.projects .arrow{color:#666;top:123px;width:18px;height:18px}

.events{height:330px}
.event-grid{display:grid;grid-template-columns:repeat(4,124px);grid-template-rows:97px 97px;gap:7px 7px;justify-content:center;margin-top:17px}
.event{background:#fff;box-shadow:0 1px 4px rgba(0,0,0,.1);padding:6px 9px}
.event__head{display:flex;gap:6px;align-items:center}
.avatar{width:15px;height:15px;border-radius:50%;border:1.2px solid #9aa1ad}
.event__name{font-size:7px;color:var(--navy);font-weight:500}
.event__date{font-size:5px;color:var(--sky)}
.event h4{font-size:7.8px;line-height:1.4;margin:6px 0 4px;font-weight:700}
.event p{font-size:6.2px;line-height:1.8;color:var(--muted)}
.event-photo--port{background:linear-gradient(180deg,#3c5ea9,#8a6b63 60%,#2e3b5a)}
.event-photo--room{background:linear-gradient(180deg,#c0c7d4,#6b7282 60%,#39404f)}

.publications{background:linear-gradient(135deg,#f1f2f4,#e2e4e8 50%,#f1f2f4);padding-top:32px;height:215px}
.pub-grid{display:flex;gap:12px;justify-content:center;margin-top:16px}
.pub{width:165px;height:116px;background:#fff;padding:8px 11px}
.pub__meta{font-size:6.8px;color:var(--navy);display:flex;gap:8px}
.pub p{font-size:6.3px;line-height:1.85;color:#5b6270;margin-top:7px;height:54px;overflow:hidden}
.pub__link{font-size:6.5px;color:var(--sky);font-weight:700;margin-top:6px}

.jobs{padding-top:70px;height:287px}
.job-grid{display:flex;gap:11px;justify-content:center;margin-top:28px}
.job{width:166px;height:104px;position:relative;text-align:center;color:#fff;padding-top:48px}
.job--navy{background:var(--navy)}
.job--sky{background:var(--sky)}
.job--soft{background:var(--sky-soft);color:var(--navy)}
.job--soft p{color:#5b6270}
.job__hex{position:absolute;left:50%;top:-30px;transform:translateX(-50%);width:62px;height:58px}
.job h3{font-size:7.8px;font-weight:700;letter-spacing:.3px}
.job p{font-size:6.8px;line-height:1.6;margin-top:6px;padding:0 14px}

.site-footer{height:85px;background:var(--navy);color:#fff;display:flex;align-items:center;padding:0 60px 0 58px}
.page--compact .site-footer{height:80px}
.footer-links{font-size:7px;word-spacing:2px}
.footer-links span{margin:0 7px;opacity:.8}
.footer-copy{font-size:6.5px;margin-top:12px}
.social{margin-left:auto;display:flex;gap:7px}
.social i{width:24px;height:24px;border:1.2px solid #fff;border-radius:50%;display:flex;align-items:center;justify-content:center}
.social i::after{content:"";width:5px;height:5px;border-radius:50%;background:#fff}
</style>
</head>
<body>

<div class="page page--hero">
  <header class="site-header">
    <div class="brand"><span class="brand__name">DPN</span><span class="brand__sub">Digital Process<br>Networks</span></div>
    <div class="header-tools"><span>Social media</span><span class="lang">DE | <b>EN</b> | FR</span><span class="search">Search</span></div>
  </header>
  <nav class="main-nav"><span class="is-active">HOME</span><span>RESEARCH</span><span>LEARNING-PLATFORM</span><span>TEACHING</span><span>TEAM</span><span>PUBLICATIONS</span><span>JOBS</span><span>PROJECTS</span><span>EVENTS</span><span>COOPERATIONS</span></nav>
  <section class="hero" role="img" aria-label="Photo of a team meeting in a bright office with city view">
    <div class="hero__box"><div class="hero__title">DPN</div><div class="hero__text">Chair in Business Administration, especially Digital Process<br>Networks at Velmont University deals</div></div>
    <div class="hero__btn">LEARN MORE ›</div>
    <span class="arrow" style="left:18px">‹</span><span class="arrow" style="right:18px">›</span>
  </section>
  <section class="welcome">
    <div class="welcome__text">
      <div class="eyebrow">WELCOME TO</div>
      <h1>DIGITAL PROCESS NETWORKS (DPN)</h1>
      <p>Chair in Business Administration, especially Digital Process Networks at Velmont University deals with the development and management of data-driven services, for instance healthcare. Directed by Prof. Dr.-Ing. <u>Tobias Renner</u>, the chair investigates how the application of experimental design methods combined with distributed, data analytic approaches lead to adaptive service designs and innovative solutions. This research is conducted in basic and applied research projects in cooperation with leading research and industry partners.</p>
    </div>
    <div class="welcome__media">
      <div class="welcome__frame"></div>
      <div class="welcome__photo" role="img" aria-label="Photo of a lecture in a seminar room"></div>
      <span class="arrow" style="left:13px">‹</span><span class="arrow" style="left:247px">›</span>
    </div>
  </section>
  <section class="lectures">
    <h2 class="section-title">LECTURES OF THE SEMESTER</h2>
    <div class="lecture-grid">
      <div class="lecture"><svg viewBox="0 0 36 32" fill="none" stroke="#0f3d9c" stroke-width="1.6"><rect x="3" y="16" width="10" height="13"/><circle cx="26" cy="22" r="5"/><circle cx="18" cy="7" r="4"/><path d="M14 22h6M18 12v4"/></svg>Service Management</div>
      <div class="lecture"><svg viewBox="0 0 36 32" fill="none" stroke="#0f3d9c" stroke-width="1.6"><circle cx="18" cy="13" r="10"/><path d="M12 13h12M18 7v12M14 23v7M22 23v7"/></svg>AI in Companies</div>
      <div class="lecture"><svg viewBox="0 0 36 32" fill="none" stroke="#0f3d9c" stroke-width="1.6"><rect x="6" y="3" width="24" height="12" rx="3"/><circle cx="13" cy="9" r="2"/><circle cx="23" cy="9" r="2"/><path d="M12 15v8h12v-8M15 23v6M21 23v6"/></svg>Service Engineering</div>
      <div class="lecture"><svg viewBox="0 0 36 32" fill="none" stroke="#0f3d9c" stroke-width="1.6"><rect x="3" y="8" width="22" height="16"/><path d="M10 29h8M14 24v5M7 19l5-5 4 3 5-6"/><circle cx="28" cy="8" r="5"/></svg>Monitoring Systems and<br>Mobile Apps</div>
    </div>
  </section>
  <section class="theses">
    <div class="theses__band"><h2 class="section-title">THESES</h2><p>The course management is managed by means of the VU learning platform. The system also enables to<br>register for the offered courses.</p></div>
    <div class="theses-cards">
      <div class="thesis"><div class="thesis__num">1</div><h3>BACHELOR</h3><p>The course management is managed by means of the VU learning platform.</p></div>
      <div class="thesis"><div class="thesis__num">5</div><h3>MASTER</h3><p>The course management is managed by means of the VU learning platform.</p></div>
    </div>
  </section>
  <section class="projects">
    <h2 class="section-title" style="font-size:19px">PROJECTS</h2>
    <div class="project-grid">
      <div class="project"><div class="project__photo project__photo--mall" role="img" aria-label="Photo of a busy shopping mall"></div><div class="project__body"><h3>PraeMedis</h3><p>From an analytical, conceptual and technical point of view, the project investigates the implementation of a situation-specifi</p></div></div>
      <div class="project"><div class="project__photo project__photo--farm" role="img" aria-label="Photo of a tractor working a crop field"></div><div class="project__body"><h3>Smart Farming World</h3><p>The objective of the research project AGRONET is to create a manufacturer-independent and thus fully compatible network of machines in crop farming through</p></div></div>
    </div>
    <span class="arrow" style="left:19px">‹</span><span class="arrow" style="right:19px">›</span>
  </section>
  <section class="events">
    <h2 class="section-title">CURRENT EVENTS</h2>
    <div class="event-grid">
      <div class="event-photo--port" role="img" aria-label="Photo of a container port at night"></div>
      <div class="event"><div class="event__head"><i class="avatar"></i><div><div class="event__name">John Doe</div><div class="event__date">1 April 2020</div></div></div><h4>Start of our research project VALTRIS</h4><p>Today our currently largest research project VALTRIS starts.</p></div>
      <div class="event"><div class="event__head"><i class="avatar"></i><div><div class="event__name">John Doe</div><div class="event__date">1 April 2020</div></div></div><h4>Start of our research project VALTRIS</h4><p>Today our currently largest research project VALTRIS starts.</p></div>
      <div class="event"><div class="event__head"><i class="avatar"></i><div><div class="event__name">John Doe</div><div class="event__date">1 April 2020</div></div></div><h4>Start of our research project VALTRIS</h4><p>Today our currently largest research project VALTRIS starts.</p></div>
      <div class="event"><div class="event__head"><i class="avatar"></i><div><div class="event__name">John Doe</div><div class="event__date">1 April 2020</div></div></div><h4>Start of our research project VALTRIS</h4><p>Today our currently largest research project VALTRIS starts.</p></div>
      <div class="event"><div class="event__head"><i class="avatar"></i><div><div class="event__name">John Doe</div><div class="event__date">1 April 2020</div></div></div><h4>Start of our research project VALTRIS</h4><p>Today our currently largest research project VALTRIS starts.</p></div>
      <div class="event-photo--room" role="img" aria-label="Photo of a workshop in a meeting room"></div>
      <div class="event"><div class="event__head"><i class="avatar"></i><div><div class="event__name">John Doe</div><div class="event__date">1 April 2020</div></div></div><h4>Start of our research project VALTRIS</h4><p>Today our currently largest research project VALTRIS starts.</p></div>
    </div>
  </section>
  <section class="publications">
    <h2 class="section-title">NEW PUBLICATIONS</h2>
    <div class="pub-grid">
      <div class="pub"><div class="pub__meta"><span>Ardel, K., &amp; Renner, T.</span><span>2020.</span></div><p>A Context-Aware Smart Retail Service Using Sensor Signals, Proceedings of the 12th Conference on Service Systems, 2020.</p><div class="pub__link">Download</div></div>
      <div class="pub"><div class="pub__meta"><span>Ardel, K., &amp; Renner, T.</span><span>2020.</span></div><p>Sensor-Based Coaching for Healthy Habits in Rural Regions, MobiCon '20 Workshop: Lessons from Mobile Health Pilots: Practical Interventions for</p><div class="pub__link">Download</div></div>
      <div class="pub"><div class="pub__meta"><span>Ardel, K., &amp; Renner, T.</span><span>2020.</span></div><p>Symposium on Applied Neural Models (ANM 2020) (ed.) Synthesis of Product Images with Textures using Adaptive Conditional Generative</p><div class="pub__link">Download</div></div>
    </div>
  </section>
  <section class="jobs">
    <h2 class="section-title">JOBS AND INTERNSHIP</h2>
    <div class="job-grid">
      <div class="job job--navy"><svg class="job__hex" viewBox="0 0 62 58"><path d="M16 2h30l15 27-15 27H16L1 29z" fill="#fff"/><circle cx="27" cy="25" r="8" fill="none" stroke="#0f3d9c" stroke-width="1.6"/><path d="M33 31l8 8" stroke="#0f3d9c" stroke-width="2"/></svg><h3>RESEARCH ASSOCIATES</h3><p>Research Assistant to support Project Management wanted!</p></div>
      <div class="job job--sky"><svg class="job__hex" viewBox="0 0 62 58"><path d="M16 2h30l15 27-15 27H16L1 29z" fill="#fff"/><path d="M19 20l12-6 12 6-12 6z" fill="none" stroke="#0f3d9c" stroke-width="1.6"/><circle cx="31" cy="31" r="5" fill="none" stroke="#0f3d9c" stroke-width="1.6"/><path d="M22 44c2-5 16-5 18 0" fill="none" stroke="#0f3d9c" stroke-width="1.6"/></svg><h3>STUDENT ASSISTANTS</h3><p>Student assistant in the field of PR and Communication wanted!</p></div>
      <div class="job job--navy"><svg class="job__hex" viewBox="0 0 62 58"><path d="M16 2h30l15 27-15 27H16L1 29z" fill="#fff"/><rect x="19" y="20" width="24" height="17" fill="none" stroke="#0f3d9c" stroke-width="1.6"/><path d="M26 20v-4h10v4M19 27h24" fill="none" stroke="#0f3d9c" stroke-width="1.6"/></svg><h3>INTERNSHIP</h3><p>Gain practical experience in an internship with us – become a member of the team!</p></div>
    </div>
  </section>
  <footer class="site-footer">
    <div><div class="footer-links">Help<span>|</span>FAQ<span>|</span>Support<span>|</span>Sitemap<span>|</span>Terms &amp; Conditions<span>|</span>Privacy Statement</div><div class="footer-copy">© 2020 DPN | All Rights Reserved</div></div>
    <div class="social" aria-label="Social media links"><i></i><i></i><i></i><i></i></div>
  </footer>
</div>

<div class="page page--compact">
  <header class="site-header">
    <div class="brand"><span class="brand__name">DPN</span><span class="brand__sub">Digital Process<br>Networks</span></div>
    <div class="header-tools"><span>Social media</span><span class="lang">DE | <b>EN</b> | FR</span><span class="search">Search</span></div>
  </header>
  <nav class="main-nav"><span class="is-active">HOME</span><span>RESEARCH</span><span>LEARNING-PLATFORM</span><span>TEACHING</span><span>TEAM</span><span>PUBLICATIONS</span><span>JOBS</span><span>PROJECTS</span><span>EVENTS</span><span>COOPERATIONS</span></nav>
  <section class="welcome">
    <div class="welcome__text">
      <div class="eyebrow">WELCOME TO</div>
      <h1>DIGITAL PROCESS NETWORKS (DPN)</h1>
      <p>Chair in Business Administration, especially Digital Process Networks at Velmont University deals with the development and management of data-driven services, for instance healthcare. Directed by Prof. Dr.-Ing. <u>Tobias Renner</u>, the chair investigates how the application of experimental design methods combined with distributed, data analytic approaches lead to adaptive service designs and innovative solutions. This research is conducted in basic and applied research projects in cooperation with leading research and industry partners.</p>
    </div>
    <div class="welcome__media">
      <div class="welcome__frame"></div>
      <div class="welcome__photo" role="img" aria-label="Photo of a lecture in a seminar room"></div>
      <span class="arrow" style="left:13px">‹</span><span class="arrow" style="left:247px">›</span>
    </div>
  </section>
  <section class="lectures">
    <h2 class="section-title">LECTURES OF THE SEMESTER</h2>
    <div class="lecture-grid">
      <div class="lecture"><svg viewBox="0 0 36 32" fill="none" stroke="#0f3d9c" stroke-width="1.6"><rect x="3" y="16" width="10" height="13"/><circle cx="26" cy="22" r="5"/><circle cx="18" cy="7" r="4"/><path d="M14 22h6M18 12v4"/></svg>Service Management</div>
      <div class="lecture"><svg viewBox="0 0 36 32" fill="none" stroke="#0f3d9c" stroke-width="1.6"><circle cx="18" cy="13" r="10"/><path d="M12 13h12M18 7v12M14 23v7M22 23v7"/></svg>AI in Companies</div>
      <div class="lecture"><svg viewBox="0 0 36 32" fill="none" stroke="#0f3d9c" stroke-width="1.6"><rect x="6" y="3" width="24" height="12" rx="3"/><circle cx="13" cy="9" r="2"/><circle cx="23" cy="9" r="2"/><path d="M12 15v8h12v-8M15 23v6M21 23v6"/></svg>Service Engineering</div>
      <div class="lecture"><svg viewBox="0 0 36 32" fill="none" stroke="#0f3d9c" stroke-width="1.6"><rect x="3" y="8" width="22" height="16"/><path d="M10 29h8M14 24v5M7 19l5-5 4 3 5-6"/><circle cx="28" cy="8" r="5"/></svg>Monitoring Systems and<br>Mobile Apps</div>
    </div>
  </section>
  <section class="theses">
    <div class="theses__band"><h2 class="section-title">THESES</h2><p>The course management is managed by means of the VU learning platform. The system also enables to<br>register for the offered courses.</p></div>
    <div class="theses-cards">
      <div class="thesis"><div class="thesis__num">1</div><h3>BACHELOR</h3><p>The course management is managed by means of the VU learning platform.</p></div>
      <div class="thesis"><div class="thesis__num">5</div><h3>MASTER</h3><p>The course management is managed by means of the VU learning platform.</p></div>
    </div>
  </section>
  <section class="projects">
    <h2 class="section-title" style="font-size:19px">PROJECTS</h2>
    <div class="project-grid">
      <div class="project"><div class="project__photo project__photo--mall" role="img" aria-label="Photo of a busy shopping mall"></div><div class="project__body"><h3>PraeMedis</h3><p>From an analytical, conceptual and technical point of view, the project investigates the implementation of a situation-specifi</p></div></div>
      <div class="project"><div class="project__photo project__photo--farm" role="img" aria-label="Photo of a tractor working a crop field"></div><div class="project__body"><h3>Smart Farming World</h3><p>The objective of the research project AGRONET is to create a manufacturer-independent and thus fully compatible network of machines in crop farming through</p></div></div>
    </div>
    <span class="arrow" style="left:19px">‹</span><span class="arrow" style="right:19px">›</span>
  </section>
  <section class="events">
    <h2 class="section-title">CURRENT EVENTS</h2>
    <div class="event-grid">
      <div class="event-photo--port" role="img" aria-label="Photo of a container port at night"></div>
      <div class="event"><div class="event__head"><i class="avatar"></i><div><div class="event__name">John Doe</div><div class="event__date">1 April 2020</div></div></div><h4>Start of our research project VALTRIS</h4><p>Today our currently largest research project VALTRIS starts.</p></div>
      <div class="event"><div class="event__head"><i class="avatar"></i><div><div class="event__name">John Doe</div><div class="event__date">1 April 2020</div></div></div><h4>Start of our research project VALTRIS</h4><p>Today our currently largest research project VALTRIS starts.</p></div>
      <div class="event"><div class="event__head"><i class="avatar"></i><div><div class="event__name">John Doe</div><div class="event__date">1 April 2020</div></div></div><h4>Start of our research project VALTRIS</h4><p>Today our currently largest research project VALTRIS starts.</p></div>
      <div class="event"><div class="event__head"><i class="avatar"></i><div><div class="event__name">John Doe</div><div class="event__date">1 April 2020</div></div></div><h4>Start of our research project VALTRIS</h4><p>Today our currently largest research project VALTRIS starts.</p></div>
      <div class="event"><div class="event__head"><i class="avatar"></i><div><div class="event__name">John Doe</div><div class="event__date">1 April 2020</div></div></div><h4>Start of our research project VALTRIS</h4><p>Today our currently largest research project VALTRIS starts.</p></div>
      <div class="event-photo--room" role="img" aria-label="Photo of a workshop in a meeting room"></div>
      <div class="event"><div class="event__head"><i class="avatar"></i><div><div class="event__name">John Doe</div><div class="event__date">1 April 2020</div></div></div><h4>Start of our research project VALTRIS</h4><p>Today our currently largest research project VALTRIS starts.</p></div>
    </div>
  </section>
  <section class="publications">
    <h2 class="section-title">NEW PUBLICATIONS</h2>
    <div class="pub-grid">
      <div class="pub"><div class="pub__meta"><span>Ardel, K., &amp; Renner, T.</span><span>2020.</span></div><p>A Context-Aware Smart Retail Service Using Sensor Signals, Proceedings of the 12th Conference on Service Systems, 2020.</p><div class="pub__link">Download</div></div>
      <div class="pub"><div class="pub__meta"><span>Ardel, K., &amp; Renner, T.</span><span>2020.</span></div><p>Sensor-Based Coaching for Healthy Habits in Rural Regions, MobiCon '20 Workshop: Lessons from Mobile Health Pilots: Practical Interventions for</p><div class="pub__link">Download</div></div>
      <div class="pub"><div class="pub__meta"><span>Ardel, K., &amp; Renner, T.</span><span>2020.</span></div><p>Symposium on Applied Neural Models (ANM 2020) (ed.) Synthesis of Product Images with Textures using Adaptive Conditional Generative</p><div class="pub__link">Download</div></div>
    </div>
  </section>
  <section class="jobs">
    <h2 class="section-title">JOBS AND INTERNSHIP</h2>
    <div class="job-grid">
      <div class="job job--soft"><svg class="job__hex" viewBox="0 0 62 58"><path d="M16 2h30l15 27-15 27H16L1 29z" fill="#fff"/><circle cx="27" cy="25" r="8" fill="none" stroke="#0f3d9c" stroke-width="1.6"/><path d="M33 31l8 8" stroke="#0f3d9c" stroke-width="2"/></svg><h3>RESEARCH ASSOCIATES</h3><p>Research Assistant to support Project Management wanted!</p></div>
      <div class="job job--sky"><svg class="job__hex" viewBox="0 0 62 58"><path d="M16 2h30l15 27-15 27H16L1 29z" fill="#fff"/><path d="M19 20l12-6 12 6-12 6z" fill="none" stroke="#0f3d9c" stroke-width="1.6"/><circle cx="31" cy="31" r="5" fill="none" stroke="#0f3d9c" stroke-width="1.6"/><path d="M22 44c2-5 16-5 18 0" fill="none" stroke="#0f3d9c" stroke-width="1.6"/></svg><h3>STUDENT ASSISTANTS</h3><p>Student assistant in the field of PR and Communication wanted!</p></div>
      <div class="job job--soft"><svg class="job__hex" viewBox="0 0 62 58"><path d="M16 2h30l15 27-15 27H16L1 29z" fill="#fff"/><rect x="19" y="20" width="24" height="17" fill="none" stroke="#0f3d9c" stroke-width="1.6"/><path d="M26 20v-4h10v4M19 27h24" fill="none" stroke="#0f3d9c" stroke-width="1.6"/></svg><h3>INTERNSHIP</h3><p>Gain practical experience in an internship with us – become a member of the team!</p></div>
    </div>
  </section>
  <footer class="site-footer">
    <div><div class="footer-links">Help<span>|</span>FAQ<span>|</span>Support<span>|</span>Sitemap<span>|</span>Terms &amp; Conditions<span>|</span>Privacy Statement</div><div class="footer-copy">© 2020 DPN | All Rights Reserved</div></div>
    <div class="social" aria-label="Social media links"><i></i><i></i><i></i><i></i></div>
  </footer>
</div>

</body>
</html>
```